Recruitment Site Design

We need a design for the login page, about page, and inner pages of a recruitment site for an oil and gas company. Design should be modern, sleek, professional and colors can be blue, green, white, orange or any other recommended colors.

Please also take into consideration that once the users login, they will need to access a form to fill in their information.

** UPDATE: Kindly provide a design for the inner information page consistent with the outer design. Attached is a picture of the basic structure. ***
Updates

Please provide a design for inner pages as shown in the design brief consistent with the registration page provided. 

Reason: We're extending it to get more inside pages.

Target Market(s)

Professionals looking for a career in the oil and gas industry in the Middle East.

Industry/Entity Type

Oil And Gas

Requirements
Must have
• Sleek design

```html
<!DOCTYPE html>
<html lang="en">
<head>
<meta charset="utf-8">
<title>Petrova — Jobs in Oil &amp; Gas</title>
<link href="https://fonts.googleapis.com/css2?family=Source+Sans+3:ital,wght@0,400;0,600;0,700;1,400&display=swap" rel="stylesheet">
<style>
:root{
  --ink:#2b2b2b;
  --dark:#1c1c1c;
  --footer:#333333;
  --teal:#17708f;
  --accent:#1aa6d6;
  --sand:#f5e6a4;
  --page-grey:#e6e6e6;
  --rule:#cfcfcf;
  --text:#444;
  --white:#fff;
}
*{margin:0;padding:0;box-sizing:border-box}
html,body{width:800px;height:1200px;overflow:hidden;background:var(--white)}
body{position:relative;font-family:"Source Sans 3",sans-serif;color:var(--ink)}
.abs{position:absolute}

/* header */
.topbar{left:0;top:0;width:500px;height:62px;background:var(--dark)}
.brand{left:86px;top:12px;font-size:34px;font-weight:400;color:var(--white);letter-spacing:1px;line-height:1}
.main-nav{left:211px;top:25px;display:flex;gap:11px;font-size:11px;color:var(--white)}
.main-nav .active{color:var(--accent)}
.phone{left:561px;top:10px;font-size:12px;color:#333}
.search{left:539px;top:43px;width:147px;height:19px;border:1px solid #c9c9c9;background:linear-gradient(#f4f4f4,#fff);font-size:7px;font-style:italic;color:#999;padding:5px 9px}
.search-btn{left:690px;top:42px;width:23px;height:21px;background:var(--accent);border-radius:2px}

/* hero */
.hero{left:0;top:66px;width:800px;height:398px;background:linear-gradient(90deg,var(--sand) 0%,#f1e29e 35%,#c9b86f 55%,#8f8f62 75%,#5c7f79 100%)}
.hero-title{left:86px;top:178px;font-size:25px;font-weight:700;color:var(--teal)}
.hero-sub{left:87px;top:212px;font-size:16px;color:var(--teal)}
.hero-copy{left:87px;top:244px;width:300px;font-size:7.3px;line-height:15px;color:var(--teal)}
.btn-more{left:86px;top:301px;width:75px;height:28px;background:#2d2d2d;border:1px solid #111;color:var(--white);font-size:12px;display:flex;align-items:center;justify-content:center;border-radius:2px}

/* grey page */
.page-bg{left:0;top:464px;width:800px;height:647px;background:var(--page-grey)}
.card{background:var(--white);border-radius:3px}
.about{left:86px;top:447px;width:627px;height:170px}
.card h2{font-size:16px;font-weight:400;color:#222}
.about h2{position:absolute;left:18px;top:16px}
.about p{position:absolute;left:18px;width:595px;font-size:7px;line-height:15.5px;color:var(--text)}
.read-more{right:20px;bottom:18px;font-size:8px;color:var(--accent)}

.lists{left:86px;top:631px;width:627px;height:340px}
.lists h2{position:absolute;top:11px}
.divider{left:330px;top:36px;width:1px;height:290px;background:var(--rule)}
.job{position:absolute;left:18px;width:300px;height:90px}
.job-photo{position:absolute;left:0;top:0;width:66px;height:54px;border-radius:2px}
.job-info{position:absolute;left:76px;top:-2px;width:225px}
.job-title{font-size:10px;color:#333}
.job-title small{font-size:8px;color:#666}
.job-loc{font-size:8.5px;color:#444;margin-top:3px}
.job-desc{font-size:6.8px;line-height:15px;color:#555;margin-top:2px}
.job-btns{display:flex;gap:12px;margin-top:4px}
.btn{width:40px;height:14px;font-size:7px;display:flex;align-items:center;justify-content:center;border-radius:1px}
.btn-details{background:#2d2d2d;color:var(--accent)}
.btn-apply{background:var(--accent);color:var(--white)}
.view-all{font-size:8.5px;font-weight:600;color:#333}

.quote{position:absolute;left:346px;width:263px;font-size:7px;font-style:italic;line-height:15.5px;color:#444}
.quote b{font-weight:400}
.byline{position:absolute;font-size:7px;text-align:right;color:#333;line-height:13px}
.avatar{position:absolute;width:66px;height:56px;border:1px solid #ddd}

.sponsors{left:86px;top:985px;width:627px;height:112px}
.sponsors h2{position:absolute;left:0;width:100%;top:13px;text-align:center;font-size:15px;color:#444}
.rule{left:18px;width:591px;height:1px;background:#bbb}
.sponsor-row{left:18px;top:50px;width:591px;height:40px;display:flex;justify-content:space-between;align-items:center}
.sponsor{display:flex;align-items:center;gap:6px;font-size:19px;font-weight:600;color:#333}
.sponsor i{display:block;width:10px;height:10px;background:#333}
.sponsor i.round{border-radius:50%}

.footer{left:86px;top:1111px;width:627px;height:52px;background:var(--footer)}
.foot-nav{left:19px;top:20px;display:flex;gap:13px;font-size:10.5px;color:var(--white)}
.socials{right:20px;top:14px;display:flex;gap:6px}
.socials span{width:23px;height:23px;border-radius:4px;background:#4f8fd1}
.legal{left:86px;top:1167px;font-size:6.5px;line-height:15px;color:#444}
.policy{right:87px;top:1177px;font-size:6.5px;color:#444}
</style>
</head>
<body>

<header>
  <div class="abs topbar"></div>
  <div class="abs brand">Petrova</div>
  <nav class="abs main-nav">
    <span class="active">About Us</span><span>Jobs</span><span>Blog</span><span>Find Now</span><span>Location</span><span>Contact</span>
  </nav>
  <div class="abs phone">Phone : 1800-2400-5500-0000</div>
  <div class="abs search">Search Here</div>
  <div class="abs search-btn">
    <svg width="23" height="21" viewBox="0 0 23 21"><circle cx="10" cy="9" r="3.5" fill="none" stroke="#fff" stroke-width="1.6"/><line x1="12.6" y1="11.6" x2="15.5" y2="14.5" stroke="#fff" stroke-width="2"/></svg>
  </div>
</header>

<section>
  <div class="abs hero" role="img" aria-label="Hazy harbour at sunset with cargo ships, a suspension bridge and mountains"></div>
  <h1 class="abs hero-title">Jobs in Oil &amp; Gas Industry</h1>
  <div class="abs hero-sub">Apply Now For Middle East Jobs</div>
  <p class="abs hero-copy">Lorem ipsum dolor sit amet, consectetur adipiscing elit. Fusce accumsan, elit a suscipit sagittis, tortor sapien cursus risus, non rhoncus lectus nunc ac nulla?<br>Aliquam molestie, mi et imperdiet euismod, dui purus auctor tellus, et interdum lacus</p>
  <div class="abs btn-more">More Info</div>
</section>

<div class="abs page-bg"></div>

<section class="abs card about">
  <h2>Little About Our Company</h2>
  <p style="top:56px">Lorem ipsum dolor sit amet, consectetur adipiscing elit. Fusce accumsan, elit a suscipit sagittis, tortor sapien cursus risus, non rhoncus lectus nunc ac nulla?<br>Aliquam molestie, mi et imperdiet euismod, dui purus auctor tellus, et interdum lacus lectus et ante. Sed accumsan sollicitudin sapien, sit amet adipiscing turpis gravida ac. In</p>
  <p style="top:118px">congue, neque ac lobortis volutpat, libero mauris varius mi, vitae suscipit ipsum ligula vitae risus. Duis aliquam nibh a dui iaculis viverra id a velit. Vivamus egestas risus in magna varius commodo. Sed semper viverra egestas. Etiam pretium porttitor lectus, vel ornare neque porta volutpat.</p>
  <div class="abs read-more">Read More..........</div>
</section>

<section class="abs card lists">
  <h2 style="left:18px">Recent Jobs</h2>

  <article class="job" style="top:37px">
    <div class="job-photo" role="img" aria-label="Engineer in a red jacket working on yellow equipment" style="background:linear-gradient(135deg,#8fb4d6,#d9a43a 60%,#b8332d)"></div>
    <div class="job-info">
      <div class="job-title">Name Job Tittle here &nbsp;<small>I &nbsp;Oil &amp; Gas Industry Company</small></div>
      <div class="job-loc">Location : &nbsp; Place of Middle East here</div>
      <div class="job-desc">Lorem ipsum dolor sit amet, consectetur adipiscing elit. Fusce accumsan, elit a suscipit sagittis, tortor sapien cursus risus, non</div>
      <div class="job-btns"><span class="btn btn-details">Details</span><span class="btn btn-apply">Apply</span></div>
    </div>
  </article>

  <article class="job" style="top:134px">
    <div class="job-photo" role="img" aria-label="Engineer reviewing technical plans" style="background:linear-gradient(135deg,#e7e3de,#c8b7a6 55%,#d68f86)"></div>
    <div class="job-info">
      <div class="job-title">Name Job Tittle here &nbsp;<small>I &nbsp;Oil &amp; Gas Industry Company</small></div>
      <div class="job-loc">Location : &nbsp; Place of Middle East here</div>
      <div class="job-desc">Lorem ipsum dolor sit amet, consectetur adipiscing elit. Fusce accumsan, elit a suscipit sagittis, tortor sapien cursus risus, non</div>
      <div class="job-btns"><span class="btn btn-details">Details</span><span class="btn btn-apply">Apply</span></div>
    </div>
  </article>

  <article class="job" style="top:233px">
    <div class="job-photo" role="img" aria-label="Workers at an industrial refinery plant" style="background:linear-gradient(135deg,#2e3f56,#7d8ea3 55%,#3a4a60)"></div>
    <div class="job-info">
      <div class="job-title">Name Job Tittle here &nbsp;<small>I &nbsp;Oil &amp; Gas Industry Company</small></div>
      <div class="job-loc">Location : &nbsp; Place of Middle East here</div>
      <div class="job-desc">Lorem ipsum dolor sit amet, consectetur adipiscing elit. Fusce accumsan, elit a suscipit sagittis, tortor sapien cursus risus, non</div>
      <div class="job-btns"><span class="btn btn-details">Details</span><span class="btn btn-apply">Apply</span></div>
    </div>
  </article>

  <div class="abs view-all" style="left:260px;top:315px">View All &gt;&gt;&gt;</div>

  <div class="abs divider"></div>

  <h2 style="left:347px">Testimonials</h2>
  <p class="quote" style="top:33px">Lorem ipsum dolor sit amet, consectetur adipiscing<br><span style="display:block;height:2px"></span>Lorem ipsum dolor sit amet, consectetur adipiscing elit. Fusce accumsan, elit a suscipit sagittis, tortor sapien cursus risus, non rhoncus lectus nunc ac nulla?</p>
  <div class="byline" style="right:99px;top:125px">By Auther Name<br>05 Nov. 2012</div>
  <div class="avatar" role="img" aria-label="Portrait of a smiling woman" style="left:541px;top:92px;background:linear-gradient(#e7c27a,#f2d2bd)"></div>

  <p class="quote" style="top:161px">Lorem ipsum dolor sit amet, consectetur adipiscing<br><span style="display:block;height:2px"></span>Lorem ipsum dolor sit amet, consectetur adipiscing elit. Fusce accumsan, elit a suscipit sagittis, tortor sapien cursus risus, non rhoncus lectus nunc ac nulla?Aliquam molestie, mi et imperdiet euismod, dui purus auctor tellus, et interdum lacus lectus et ante.</p>
  <div class="byline" style="right:99px;top:283px">By Auther Name<br>05 Nov. 2012</div>
  <div class="avatar" role="img" aria-label="Portrait of a smiling man" style="left:541px;top:250px;background:linear-gradient(#b9b4ad,#d7a888)"></div>

  <div class="abs view-all" style="left:555px;top:315px">View All &gt;&gt;&gt;</div>
</section>

<section class="abs card sponsors">
  <h2>Our Sponsors</h2>
  <div class="abs rule" style="top:37px"></div>
  <div class="abs sponsor-row">
    <div class="sponsor"><i></i>Norvia</div>
    <div class="sponsor">Kestrel</div>
    <div class="sponsor"><i class="round"></i>Dalto</div>
    <div class="sponsor">Ferron</div>
    <div class="sponsor">Lumara</div>
    <div class="sponsor"><i class="round"></i>Quillon</div>
  </div>
  <div class="abs rule" style="top:91px"></div>
</section>

<footer>
  <div class="abs footer">
    <nav class="abs foot-nav"><span>About Us</span><span>Jobs</span><span>Blog</span><span>Find Now</span><span>Location</span><span>Contact</span></nav>
    <div class="abs socials" aria-label="Social links"><span></span><span style="background:#c9423a"></span><span style="background:#5ab7e6"></span><span style="background:#ef8a2c"></span><span style="background:#2a7fb8"></span></div>
  </div>
  <div class="abs legal">© &nbsp;2012 Petrova<br>All right reserved</div>
  <div class="abs policy">Privacy / Policy</div>
</footer>

</body>
</html>
```